Brightfield Ventures Inc. Letterhead

Creation of attractive and eye catching letterhead for a business start-up for the construction industry. Letterhead must relate to construction, but avoid standard hammer and tools in the design.

I forgot to add some details, sorry about that. Some pertinent info: Ph: 916-555-0187 brightfieldventures.example 448 Willowmere Ave, Ste 210 Folsom, CA 95999 info@brightfieldventures.example not sure if slogan should be in there" “Connecting construction professionals to create a purpose driven industry.” must be able to be used in word. Thanks!

```html
<!DOCTYPE html>
<html lang="en">
<head>
<meta charset="utf-8">
<title>Brightfield Ventures Inc. Letterhead</title>
<link href="https://fonts.googleapis.com/css2?family=Open+Sans:wght@400;600&family=Montserrat:wght@600&family=Arimo:wght@700&display=swap" rel="stylesheet">
<style>
  :root {
    --backdrop: #ececee;
    --paper: #ffffff;
    --brand-red: #c00a0a;
    --brand-navy: #14275e;
    --ink: #2b2b2b;
    --muted: #555a63;
    --signature-tone: #e4e4e6;
  }
  * { box-sizing: border-box; margin: 0; padding: 0; }
  html, body {
    width: 1200px; height: 784px; overflow: hidden;
    background: var(--backdrop);
  }
  .letterhead {
    position: absolute; left: 323px; top: 0;
    width: 554px; height: 784px;
    background: var(--paper);
    box-shadow: 0 2px 10px rgba(0,0,0,0.12);
    overflow: hidden;
    font-family: "Open Sans", Arial, sans-serif;
    color: var(--ink);
  }
  .brand {
    position: absolute; left: 44px; top: 56px;
    display: flex; align-items: center; gap: 8px;
  }
  .brand-mark {
    width: 14px; height: 14px; background: var(--brand-red);
  }
  .brand-name {
    font-family: "Montserrat", Arial, sans-serif;
    font-weight: 600; font-size: 13px; letter-spacing: 0.06em;
    color: var(--brand-navy); text-transform: uppercase;
  }
  .brand-rule {
    position: absolute; left: 44px; top: 80px;
    width: 160px; height: 1px; background: var(--brand-red);
  }
  .contact {
    position: absolute; right: 40px; top: 48px;
    list-style: none; font-size: 7.5px; line-height: 12px; color: var(--muted);
  }
  .contact li { display: flex; align-items: center; gap: 5px; }
  .contact svg { width: 7px; height: 7px; fill: var(--brand-red); flex: none; }
  .contact .no-icon { padding-left: 12px; }
  .salutation {
    position: absolute; left: 60px; top: 150px;
    font-family: "Arimo", Arial, sans-serif; font-weight: 700; font-size: 13px;
  }
  .letter-body {
    position: absolute; left: 60px; top: 180px; width: 430px;
    font-size: 10px; line-height: 15px;
  }
  .letter-body p + p { margin-top: 14px; }
  .signature {
    position: absolute; left: 60px; top: 520px;
    width: 120px; height: 50px; background: var(--signature-tone);
  }
  .swoosh { position: absolute; left: 0; top: 0; width: 554px; height: 784px; }
</style>
</head>
<body>
  <main class="letterhead">
    <div class="brand">
      <span class="brand-mark"></span>
      <span class="brand-name">Brightfield Ventures Inc.</span>
    </div>
    <div class="brand-rule"></div>

    <ul class="contact">
      <li><svg viewBox="0 0 10 10"><path d="M2 0 L4 2.5 L3 3.8 Q4.5 6 6.2 7 L7.5 6 L10 8 L8.5 10 Q3 9 0 1.5 Z"/></svg>Ph: 916-555-0187</li>
      <li><svg viewBox="0 0 10 10"><path d="M0 2 H10 V8 H0 Z M0 2 L5 6 L10 2"/></svg>info@brightfieldventures.example</li>
      <li><svg viewBox="0 0 10 10"><circle cx="5" cy="5" r="5"/></svg>brightfieldventures.example</li>
      <li class="no-icon">448 Willowmere Ave, Ste 210</li>
      <li class="no-icon">Folsom, CA 95999</li>
    </ul>

    <h1 class="salutation">Dear Mr. Harlow,</h1>

    <section class="letter-body">
      <p>Lorem Ipsum is simply dummy text of the printing and typesetting industry. Lorem Ipsum has been the industry's standard dummy text ever since the 1500s, when an unknown printer took a galley of type and scrambled it to make a type specimen book. It has survived not only five centuries, but also the leap into electronic typesetting, remaining essentially unchanged.</p>
      <p>The standard chunk of Lorem Ipsum used since the 1500s is reproduced below for those interested. Sections 1.10.32 and 1.10.33 from "de Finibus Bonorum et Malorum" by L. Tarvo are also reproduced in their exact original form, accompanied by English versions from the 1914 translation by H. Ellery.</p>
      <p>Lorem Ipsum is simply dummy text of the printing and typesetting industry. Lorem Ipsum has been the industry's standard dummy text ever since the 1500s, when an unknown printer took a galley of type and scrambled it to make a type specimen book. It has survived not only five centuries, but also the leap into electronic typesetting, remaining essentially unchanged. It was popularised in the</p>
      <p>The standard chunk of Lorem Ipsum used since the 1500s is reproduced below for those interested. Sections 1.10.32 and 1.10.33 from "de Finibus Bonorum et Malorum" by L. Tarvo are also reproduced in their exact original form, accompanied by English versions from the 1914 translation by H. Ellery.</p>
    </section>

    <div class="signature" role="img" aria-label="Handwritten signature of the sender"></div>

    <svg class="swoosh" viewBox="0 0 554 784" aria-hidden="true">
      <path d="M130 784 C 290 735, 410 640, 462 552 C 492 500, 515 462, 554 428" fill="none" stroke="var(--brand-navy)" stroke-width="3"/>
      <path d="M150 784 C 300 742, 420 652, 470 562 C 500 508, 522 472, 554 442 L 554 784 Z" fill="var(--brand-red)"/>
    </svg>
  </main>
</body>
</html>
```